Card design for orthopaedic surgeons working as The Brightwater Joint Centre

Business cards, letterhead

Colors

Designer to choose colors to be used in the design.

Requirements
Must have
• Late addition.
• Cards letterhead must have logos of
• Crestmoor Lindell College of Surgeons
• Varenwood Bone Health Association
Nice to have
• Back of card to have space for appointment time to be added by hand and some blank space for writing incidental other notes.

```html
<!DOCTYPE html>
<html lang="en">
<head>
<meta charset="utf-8">
<title>The Brightwater Joint Centre – Stationery</title>
<link href="https://fonts.googleapis.com/css2?family=Didact+Gothic&family=Source+Sans+3:ital,wght@0,400;0,600;1,400&display=swap" rel="stylesheet">
<style>
  :root{
    --bg:#dcdcdc;
    --paper:#ffffff;
    --sky:#33adf7;
    --navy:#0c2d48;
    --ink:#333b44;
    --muted:#55595e;
  }
  *{margin:0;padding:0;box-sizing:border-box}
  html,body{width:1200px;height:877px;overflow:hidden;background:var(--bg)}
  body{position:relative;font-family:"Didact Gothic",sans-serif;color:var(--ink)}
  .sheet{position:absolute;background:var(--paper);overflow:hidden}
  .brand{position:absolute;color:var(--sky);white-space:nowrap;letter-spacing:-.2px}

  /* footer band: plain blue block with a thin navy rule above */
  .band{position:absolute;left:0;right:0;bottom:0;background:var(--sky)}
  .band-rule{position:absolute;left:0;right:0;height:2px;background:var(--navy)}

  /* business card front */
  .card-front{left:118px;top:271px;width:368px;height:210px;border-radius:14px}
  .card-front .brand{left:21px;top:49px;font-size:13.5px}
  .card-front .band{top:128px}
  .card-front .band-rule{top:123px}
  .holder-name{position:absolute;left:0;top:90px;width:192px;text-align:center;font-family:"Source Sans 3",sans-serif;font-weight:600;font-size:13.5px;color:var(--sky)}
  .holder-role{position:absolute;left:0;top:106px;width:192px;text-align:center;font-size:9px;color:#111}
  .contact{position:absolute;right:22px;text-align:right;color:#fff;font-size:9.2px;line-height:9.8px}
  .contact .row{display:flex;justify-content:flex-end;align-items:center;gap:4px;white-space:nowrap}
  .contact .gap{height:4px}
  .icon{width:7px;height:7px;fill:#fff;flex:none}
  .icon-blank{width:7px;flex:none}

  /* appointment card */
  .card-back{left:118px;top:530px;width:368px;height:209px;border-radius:14px;font-family:"Source Sans 3",sans-serif;color:var(--sky)}
  .appt-title{position:absolute;top:30px;left:0;width:100%;text-align:center;font-weight:600;font-size:14.5px}
  .fill{position:absolute;font-size:10.5px;display:flex;align-items:baseline;white-space:nowrap}
  .dots{border-bottom:1px dotted #777;display:inline-block;height:1px;margin:0 3px}
  .days{position:absolute;top:141px;left:24px;width:326px;display:flex;justify-content:space-between;font-size:9.5px}
  .day{display:flex;align-items:center;gap:5px}
  .box{width:9px;height:8px;border:1.2px solid var(--navy)}
  .notice{position:absolute;top:175px;left:0;width:100%;text-align:center;font-style:italic;font-size:8px;line-height:10.5px;color:var(--muted)}

  /* letterhead */
  .letterhead{left:557px;top:69px;width:527px;height:742px}
  .letterhead .brand{left:46px;top:67px;font-size:12.5px}
  .letterhead .band{top:650px}
  .letterhead .band-rule{top:645px}
  .salutation{position:absolute;left:46px;top:207px;font-size:13.5px;color:#333}
  .body-copy{position:absolute;left:46px;top:246px;width:440px;font-size:7.9px;line-height:11.45px;color:#333;text-align:justify}
  .body-copy p{margin-bottom:11.4px}
  .closing{position:absolute;left:46px;top:486px;font-size:7.6px;color:#333}
  .signature{position:absolute;left:46px;top:515px;width:60px;height:26px;background:linear-gradient(90deg,#eef1f4,#e2e7ec);border-radius:3px}
  .letterhead .contact{right:36px;top:660px;font-size:7.8px;line-height:10px;letter-spacing:.3px}
</style>
</head>
<body>

<svg width="0" height="0" style="position:absolute" aria-hidden="true">
  <symbol id="i-phone" viewBox="0 0 10 10"><path d="M2 0.5 L3.6 0.5 L4.3 3 L3.1 3.9 Q4.2 6 6.1 6.9 L7 5.7 L9.5 6.4 L9.5 8 Q9.5 9.5 8 9.5 Q0.5 9 0.5 2 Q0.5 0.5 2 0.5Z"/></symbol>
  <symbol id="i-mobile" viewBox="0 0 10 10"><path d="M2.5 0 H7.5 V10 H2.5Z M3.5 1 V8 H6.5 V1Z"/></symbol>
  <symbol id="i-fax" viewBox="0 0 10 10"><path d="M2.5 0 H7.5 V3 H2.5Z M0 3.5 H10 V8 H8 V6.5 H2 V8 H0Z M2.5 7 H7.5 V10 H2.5Z"/></symbol>
  <symbol id="i-mail" viewBox="0 0 10 10"><path d="M0 2 H10 V8.5 H0Z"/><path d="M0.5 2.5 L5 5.8 L9.5 2.5" stroke="#33adf7" stroke-width="1" fill="none"/></symbol>
  <symbol id="i-globe" viewBox="0 0 10 10"><circle cx="5" cy="5" r="5"/><path d="M1 5 H9 M5 1 V9" stroke="#33adf7" stroke-width="0.9"/></symbol>
</svg>

<!-- Business card: front -->
<section class="sheet card-front">
  <div class="band-rule"></div>
  <div class="band"></div>
  <div class="brand">The Brightwater Joint Centre</div>
  <div class="holder-name">Daniel Harrow</div>
  <div class="holder-role">President</div>
  <div class="contact" style="top:133px">
    <div class="row">4120 Larkspur Row<span class="icon-blank"></span></div>
    <div class="row">Fairhaven, Oregon 97730<span class="icon-blank"></span></div>
    <div class="gap"></div>
    <div class="row">555-214-0186 <svg class="icon"><use href="#i-phone"/></svg></div>
    <div class="row">555-318-0427 <svg class="icon"><use href="#i-mobile"/></svg></div>
    <div class="row">555-406-0193 <svg class="icon"><use href="#i-fax"/></svg></div>
    <div class="row">hello@brightwaterjoint.com <svg class="icon"><use href="#i-mail"/></svg></div>
    <div class="row">www.brightwaterjoint.com <svg class="icon"><use href="#i-globe"/></svg></div>
  </div>
</section>

<!-- Business card: back -->
<section class="sheet card-back">
  <h2 class="appt-title">Next Appointment</h2>
  <div class="fill" style="top:70px;left:23px"><span class="dots" style="width:216px"></span>has an appointment</div>
  <div class="fill" style="top:103px;left:21px">Date :<span class="dots" style="width:145px;margin-left:8px"></span>Time :<span class="dots" style="width:80px"></span><span style="font-size:8px">AM/PM</span></div>
  <div class="days">
    <span class="day">Sun <i class="box"></i></span>
    <span class="day">Mon <i class="box"></i></span>
    <span class="day">Tue <i class="box"></i></span>
    <span class="day">Wed <i class="box"></i></span>
    <span class="day">Thu <i class="box"></i></span>
    <span class="day">Fri <i class="box"></i></span>
    <span class="day">Sat <i class="box"></i></span>
  </div>
  <p class="notice">Please give me 24 hours notice if you are unable to keep your appointment or<br>a cancellation fee may be charged.</p>
</section>

<!-- Letterhead -->
<section class="sheet letterhead">
  <div class="band-rule"></div>
  <div class="band"></div>
  <div class="brand">The Brightwater Joint Centre</div>
  <div class="salutation">Dear Mr. Harrow,</div>
  <div class="body-copy">
    <p>Lorem ipsum dolor sit amet, consectetur adipiscing elit. Donec orci purus, luctus vitae dignissim eu, iaculis sed purus. Vivamus faucibus, ipsum nec aliquet viverra, leo mauris condimentum ligula, sit amet sagittis enim ligula quis arcu. Nam egestas tortor id nisi porttitor mattis. In tortor ante, ultricies in suscipit a, tempus non massa. Vivamus et auctor mi. Fusce vel massa nulla. Phasellus nec eros mauris, et scelerisque orci.</p>
    <p>Donec malesuada orci vitae nulla accumsan porta a id massa. Quisque accumsan iaculis magna sit amet fringilla. Maecenas consequat, magna eget tincidunt semper, odio nibh rutrum mi, id feugiat ante nisi eu risus. Vestibulum nunc orci, rhoncus a placerat in, ultricies in mi. Cras mattis varius eros, vel fringilla nisi suscipit eget. Quisque scelerisque sagittis nulla at porttitor.</p>
    <p>Sed id augue vitae urna euismod commodo aliquet a quam. Pellentesque arcu velit, cursus et malesuada ut, consequat et diam. Nullam erat sem, rhoncus id ullamcorper vitae, rhoncus et arcu. In ultricies ultricies nulla, ut rutrum nisi iaculis at. Donec eu magna a metus ornare faucibus. Fusce aliquet faucibus ultricies. Morbi semper, est id tincidunt gravida, sem arcu adipiscing lacus, ac bibendum nulla leo eu purus. Quisque nec diam sed risus consectetur a ccumsan quis quis nibh. Vestibulum id purus lorem.</p>
    <p>It is a long established fact that a reader will be distracted by the readable content of a page when looking at its layout. The point of using Lorem Ipsum is that it has a more-or-less normal distribution of letters, as opposed to using 'Content here, content here', making it look like readable English. Many desktop publishing packages</p>
  </div>
  <div class="closing">Sincerely,</div>
  <div class="signature" role="img" aria-label="Handwritten signature of the sender"></div>
  <div class="contact">
    <div class="row">4120 Larkspur Row</div>
    <div class="row">Fairhaven, Oregon 97730</div>
    <div class="gap"></div>
    <div class="row">555-214-0186 <svg class="icon"><use href="#i-phone"/></svg></div>
    <div class="row">555-318-0427 <svg class="icon"><use href="#i-mobile"/></svg></div>
    <div class="row">555-406-0193 <svg class="icon"><use href="#i-fax"/></svg></div>
    <div class="row">daniel@brightwaterjoint.com <svg class="icon"><use href="#i-mail"/></svg></div>
    <div class="row">www.brightwaterjoint.com <svg class="icon"><use href="#i-globe"/></svg></div>
  </div>
</section>

</body>
</html>
```